Business Cards for new orthopaedic surgery practice

My husband and I are starting our own orthopaedic surgery practice. We are looking for a business card that is uniform, but one will have my name/title and the other will have his. You can just create one design with my name on it for now. But when I choose your design as the winning design I will ask that you add another copy with his name/title.

We are looking for classy, simple, elite all in one. We like dark blues/a little gold/yellow. Something that goes with our logo. We want our logo incorporated. Here is all the info you need:
Business name: RV Bone & Vitality Center
Location: 38517 North Willowmere Ave
Palm Hollow, FL 33482
Phone: 954-218-4063
Fax: 954-582-7341
Email: info@myrvbonecare.example

Names: Lydia Vance, M.D.
Board Certified Hand and Upper Extremity Surgeon

Ebo Dansu, M.D.
Board Certified Hip & Knee Replacement/General Orthopaedic Surgeon

Can decide what you want to put on the back. Maybe a slogan:
Steady in Care. Devoted to You

I am just going to upload our logo. The only thing is if we select you as the winning design, the location, and phone numbers may change. We will need your help to update that once fully solidified.

Industry/Entity Type

Medical

Contact Information for Business Card

Colors
0054AA
0677BA
7BADD7
CADEEF
E8F1F8
0094D4
00A9DD
6FCCEA
C7EBF8
E9F6FB

Requirements
Must have
• class, appeal,
Should not have
• We want to air on the side of masculine if we are looking at masculine vs. feminine feel. But we still want it classy, sophisticated, and something we will love

```html
<!DOCTYPE html>
<html lang="en">
<head>
<meta charset="utf-8">
<title>Lydia Vance, M.D. – Business Card</title>
<link rel="stylesheet" href="https://fonts.googleapis.com/css2?family=Montserrat:wght@500;600&display=swap">
<style>
  :root {
    --backdrop: #e9e7e3;
    --card-face: #f3f2ef;
    --card-edge: #dcd9d3;
    --navy: #1c2857;
    --navy-deep: #16204a;
    --gold: #c28f3d;
    --gold-bright: #c99437;
    --band-text: #e6e9f2;
    --seal-face: #f6f4ef;
  }
  * { margin: 0; padding: 0; box-sizing: border-box; }
  html, body { width: 1200px; height: 887px; overflow: hidden; }
  body {
    background: var(--backdrop);
    font-family: "Montserrat", Arial, sans-serif;
    position: relative;
  }
  .business-card {
    position: absolute;
    left: 80px; top: 150px;
    width: 1040px; height: 587px;
    background: var(--card-face);
    border: 1px solid var(--card-edge);
    border-radius: 26px;
    overflow: hidden;
  }
  .identity { position: absolute; left: 56px; top: 52px; }
  .identity__name {
    font-weight: 600; font-size: 37px; letter-spacing: 1.5px;
    color: var(--gold); text-transform: uppercase; line-height: 1.1;
  }
  .identity__title {
    margin-top: 4px;
    font-weight: 500; font-size: 22px; line-height: 29px;
    color: var(--navy);
  }
  .info-band {
    position: absolute; left: 0; top: 254px;
    width: 100%; height: 284px;
    background: linear-gradient(90deg, var(--navy-deep) 0%, var(--navy) 58%, #2a3560 76%, #8a6d3f 90%, var(--gold-bright) 100%);
  }
  .contact-list {
    position: absolute; left: 50px; top: 18px;
    list-style: none;
    color: var(--band-text);
    font-weight: 500; font-size: 22px; line-height: 29px;
  }
  .contact-list li { display: flex; align-items: center; gap: 9px; }
  .contact-list svg { width: 20px; height: 20px; flex: none; }
  .contact-list .accent { color: var(--gold-bright); }
  .address {
    position: absolute; left: 50px; top: 155px;
    color: var(--band-text);
    font-style: normal;
    font-weight: 500; font-size: 22px; line-height: 29px;
  }
  .slogan {
    position: absolute; left: 50px; top: 231px;
    color: var(--gold-bright);
    font-weight: 500; font-size: 22px; line-height: 29px;
  }
  .practice-seal {
    position: absolute; left: 713px; top: -6px;
    width: 292px; height: 292px;
    border-radius: 50%;
    background: var(--seal-face);
    display: flex; align-items: center; justify-content: center;
    text-align: center;
    padding: 40px;
  }
  .practice-seal__name {
    color: var(--navy);
    font-weight: 600; font-size: 27px; line-height: 36px;
  }
</style>
</head>
<body>
  <article class="business-card">
    <header class="identity">
      <h1 class="identity__name">Lydia Vance, M.D</h1>
      <p class="identity__title">Board Certified Hand and<br>Upper Extremity Surgeon</p>
    </header>

    <section class="info-band">
      <ul class="contact-list">
        <li>
          <svg viewBox="0 0 24 24" aria-hidden="true"><path fill="#c99437" d="M6.6 10.8a15.1 15.1 0 0 0 6.6 6.6l2.2-2.2a1 1 0 0 1 1-.25 11.4 11.4 0 0 0 3.6.57 1 1 0 0 1 1 1V20a1 1 0 0 1-1 1A17 17 0 0 1 3 4a1 1 0 0 1 1-1h3.5a1 1 0 0 1 1 1c0 1.25.2 2.45.57 3.57a1 1 0 0 1-.25 1z"/></svg>
          954-218-4063
        </li>
        <li>
          <svg viewBox="0 0 24 24" aria-hidden="true" fill="none" stroke="#c99437" stroke-width="1.8"><rect x="6" y="3" width="12" height="6"/><rect x="3" y="9" width="18" height="8" rx="1.5"/><rect x="6" y="14" width="12" height="7"/></svg>
          954-582-7341
        </li>
        <li>
          <svg viewBox="0 0 24 24" aria-hidden="true" fill="none" stroke="#c99437" stroke-width="1.8"><rect x="3" y="5.5" width="18" height="13" rx="1"/><path d="M3.5 6.5 12 13l8.5-6.5"/></svg>
          info@myrvbonecare.example
        </li>
        <li>
          <svg viewBox="0 0 24 24" aria-hidden="true" fill="none" stroke="#c99437" stroke-width="1.6"><circle cx="12" cy="12" r="9"/><ellipse cx="12" cy="12" rx="4" ry="9"/><path d="M3 12h18M5 7h14M5 17h14"/></svg>
          <span>www.<span class="accent">myrvbonecare</span>.example</span>
        </li>
      </ul>

      <address class="address">
        38517 North Willowmere Ave<br>Palm Hollow, FL 33482
      </address>

      <p class="slogan">Steady in Care. Devoted to You</p>

      <div class="practice-seal">
        <span class="practice-seal__name">RV Bone &amp; Vitality Center</span>
      </div>
    </section>
  </article>
</body>
</html>
```